Brightfield Homes needs a web design and brand identifier

Brightfield Homes is a pioneering approach by Victorian councils and four greenhouse alliances to support low income households to install solar systems with no upfront costs.

Brightfield Homes will commence in May 2017.

Brightfield Homes is looking for a designer to create a website banner incorporating a brand identifier for Brightfield Homes. The brand identifier will be used in Brightfield Homes promotional materials, such as flyers and mail outs.

The website banner and brand identifier should engender trust and confidence in the target group (retirees).

Reason: Hi, Thank you for your work so far. We've been given advice to get a separate logo designed (instead of trying to include this as part of the banner design). Sorry for not realising this until now - we're new to all this. So, I have a couple of preliminary logo designs that are being considered by our project control group. I will forward a copy of the logo once we have it. The project control group is looking for a web design that is unique to Brightfield Homes and a design that draws on the key elements of the program (i.e. it helps people save money and take control). The site should be friendly but not too informal as the target group is seniors. Here's a link to another community energy organisation: www.kindlewattnet.com.au/ Apologies again for the delays. Cheers, Doug

Target Market(s)

Home owning, low income, retirees

Industry/Entity Type

Non Profit

Number of Pages Required

1 page

Font styles to use
Sans Serif

Requirements
Must have
• Use of Brightfield Home name
• Must promote Brightfield Homes as safe, reliable and trustworthy
Nice to have
• Blue - to engender sense of safety and confidence (open to suggestions, though)
• Solar panels / the sun
Should not have
• Anything that is hard to read
• anything that promotes riskyness

```html
<!DOCTYPE html>
<html lang="en">
<head>
<meta charset="utf-8">
<title>Brightfield Homes</title>
<link href="https://fonts.googleapis.com/css2?family=Open+Sans:ital,wght@0,400;0,600;0,700;1,400&family=Roboto:wght@400;500;700&family=Roboto+Condensed:wght@700&display=swap" rel="stylesheet">
<style>
:root{
  --blue:#1f93e6;
  --blue-light:#2ba3ef;
  --blue-dark:#1a4f9c;
  --orange:#f7931e;
  --ink:#3a3a3a;
  --body:#555;
  --muted:#777;
  --line:#dcdcdc;
  --footer:#f1f1f1;
  --white:#fff;
  --slate:#2d3a52;
}
*{margin:0;padding:0;box-sizing:border-box}
html,body{width:1200px;height:2490px;overflow:hidden;background:var(--white)}
body{font-family:"Open Sans",Arial,sans-serif;color:var(--body);position:relative}
.top-line{position:absolute;top:0;left:0;width:1200px;height:3px;background:var(--blue)}
.phone-tab{position:absolute;top:0;left:923px;width:184px;height:36px;background:var(--blue);border-radius:0 0 30px 30px;color:var(--white);font-family:"Roboto",sans-serif;font-size:15px;display:flex;align-items:center;justify-content:center;gap:10px}
.header{position:absolute;top:0;left:0;width:1200px;height:108px}
.brand{position:absolute;display:flex;align-items:center;gap:10px;font-family:"Roboto",sans-serif;font-weight:700;color:var(--blue-dark)}
.brand .dot{width:22px;height:22px;border-radius:50%;background:var(--orange)}
.header .brand{left:100px;top:48px;font-size:27px}
.nav{position:absolute;top:55px;left:500px;display:flex;gap:0;list-style:none;font-family:"Roboto",sans-serif;font-size:12.5px;color:#444}
.nav li{height:33px;line-height:33px;padding:0 22px;margin-right:7px;text-transform:uppercase}
.nav li.active{background:var(--orange);color:var(--white);border-radius:18px;padding:0 20px}
.hero{position:absolute;top:108px;left:0;width:1200px;height:528px;background:linear-gradient(180deg,#5b8fc4 0%,#9cc3e8 38%,#a9c46b 62%,#6f9a35 100%)}
.hero-panels{position:absolute;left:0;top:0;width:650px;height:528px;background:linear-gradient(135deg,#1b3f86,#3f6fb8 60%,#7da2d2)}
.hero-copy{position:absolute;left:782px;top:170px;color:var(--white)}
.hero-copy h1{font-family:"Roboto Condensed",sans-serif;font-size:50px;letter-spacing:.5px;line-height:1}
.hero-copy p{font-family:"Roboto",sans-serif;font-weight:700;font-size:14px;line-height:20px;margin-top:16px;text-transform:uppercase}
.btn-outline{display:inline-block;margin-top:12px;background:var(--blue);border:2px solid var(--white);color:var(--white);font-family:"Roboto",sans-serif;font-weight:500;font-size:13px;padding:7px 14px;border-radius:3px}
.slider-arrow{position:absolute;top:240px;width:34px;height:34px;border-radius:50%;background:rgba(0,0,0,.35);display:flex;align-items:center;justify-content:center}
.features{position:absolute;top:562px;left:98px;width:1002px;height:188px;display:flex;box-shadow:0 30px 30px -18px rgba(0,0,0,.25)}
.feature{flex:1;background:var(--blue);padding:38px 22px 0 115px;position:relative;color:var(--white)}
.feature+.feature{background:var(--blue-light)}
.feature svg{position:absolute;left:18px;top:40px}
.feature h3{font-family:"Roboto",sans-serif;font-weight:500;font-size:18px;margin-bottom:12px}
.feature p{font-size:11.5px;line-height:21px}
.welcome{position:absolute;top:805px;left:0;width:1200px;text-align:center}
.welcome h2{font-family:"Roboto",sans-serif;font-weight:500;font-size:38px;color:var(--ink)}
.welcome h2 span{color:var(--blue)}
.welcome p{width:880px;margin:20px auto 0;font-size:11.5px;line-height:22px;color:var(--muted)}
.cards{position:absolute;top:970px;left:98px;width:1004px;display:flex;gap:27px}
.card{width:317px}
.card .photo{height:185px;border:4px solid var(--white);box-shadow:0 0 0 1px var(--line)}
.card h4{font-family:"Roboto",sans-serif;font-weight:400;font-size:17px;color:var(--ink);margin:25px 0 10px}
.card p{font-size:11.5px;line-height:21px;color:var(--muted)}
.how{position:absolute;top:1344px;left:0;width:1200px;height:412px;background:linear-gradient(180deg,#4a5874,#2d3a52 55%,#3b4a68);color:var(--white)}
.how h2{text-align:center;padding-top:65px;font-family:"Roboto",sans-serif;font-weight:400;font-size:29px}
.steps{position:absolute;top:148px;left:243px;width:720px;display:grid;grid-template-columns:1fr 1fr;column-gap:90px;row-gap:32px}
.step{display:flex;gap:20px;font-size:12.5px;line-height:20px}
.step svg{flex:none;margin-top:4px}
.btn-pill{position:absolute;top:305px;left:505px;width:190px;height:40px;border:2px solid var(--white);border-radius:22px;background:#3b6fc7;color:var(--white);font-family:"Roboto",sans-serif;font-weight:500;font-size:16px;display:flex;align-items:center;justify-content:center}
.news{position:absolute;top:1812px;left:98px;width:1004px}
.news h2{font-family:"Roboto",sans-serif;font-weight:400;font-size:27px;color:var(--ink)}
.news-nav{position:absolute;right:0;top:6px;display:flex;gap:10px}
.news-list{display:flex;gap:40px;margin-top:36px}
.news-item{flex:1;display:flex;gap:27px}
.news-item .photo{width:188px;height:188px;border-radius:50%;border:4px solid var(--white);box-shadow:0 0 0 1px var(--line);flex:none}
.news-item h3{font-family:"Roboto",sans-serif;font-weight:400;font-size:16px;color:var(--ink);margin-top:8px}
.news-item time{display:block;font-size:12px;font-style:italic;color:var(--blue);margin:16px 0 8px}
.news-item p{font-size:11.5px;line-height:21px;color:var(--muted)}
.news-item .more{display:block;margin-top:8px;font-size:13px;color:var(--ink)}
.footer{position:absolute;top:2152px;left:0;width:1200px;height:288px;background:var(--footer)}
.footer .brand{left:100px;top:56px;font-size:24px}
.footer-about{position:absolute;left:100px;top:110px;width:250px;font-size:12px;line-height:21px;color:var(--body)}
.socials{position:absolute;left:100px;top:180px;display:flex;gap:6px}
.socials span{width:24px;height:24px;border-radius:50%;border:1.5px solid #555}
.footer h4{font-family:"Roboto",sans-serif;font-weight:500;font-size:17px;color:var(--ink);position:absolute;top:47px;text-transform:uppercase}
.col-news h4{left:398px}
.col-news p{position:absolute;left:398px;top:84px;width:245px;font-size:11.5px;line-height:20px}
.col-news .field{position:absolute;left:398px;top:128px;width:245px;height:42px;background:var(--white);border:1px solid var(--line);font-size:11.5px;padding:13px 14px;color:#666}
.col-news .btn{position:absolute;left:398px;top:186px;width:122px;height:34px;background:var(--blue);color:var(--white);font-family:"Roboto",sans-serif;font-size:13px;display:flex;align-items:center;justify-content:center}
.col-contact h4{left:712px}
.contact-row{position:absolute;left:712px;display:flex;gap:14px;font-size:12.5px;line-height:21px;color:var(--body)}
.col-links h4{left:995px}
.col-links ul{position:absolute;left:997px;top:92px;list-style:none;font-size:11.5px;line-height:25.5px;color:var(--body)}
.bottom-bar{position:absolute;top:2440px;left:0;width:1200px;height:50px;border-top:1px solid var(--line);text-align:center;font-size:11.5px;line-height:44px;color:var(--body)}
</style>
</head>
<body>
<div class="top-line"></div>
<header class="header">
  <div class="brand"><span class="dot"></span>Brightfield Homes</div>
  <ul class="nav">
    <li class="active">Home</li><li>About Us</li><li>Our Services</li><li>How It Works</li><li>Blog</li><li>Contact Us</li>
  </ul>
</header>
<div class="phone-tab">
  <svg width="16" height="16" viewBox="0 0 24 24"><circle cx="12" cy="12" r="11" fill="none" stroke="#fff" stroke-width="2"/><path d="M8 7c0 5 4 9 9 9l1-2-3-1-1 1c-2-1-3-2-4-4l1-1-1-3z" fill="#fff"/></svg>
  0400 555 217
</div>

<section class="hero">
  <div class="hero-panels" role="img" aria-label="Rows of solar panels under a bright sun"></div>
  <div style="position:absolute;inset:0" role="img" aria-label="Green grass field under a blue sky"></div>
  <a class="slider-arrow" style="left:32px"><svg width="12" height="12" viewBox="0 0 12 12"><path d="M8 1L3 6l5 5" stroke="#fff" stroke-width="2" fill="none"/></svg></a>
  <a class="slider-arrow" style="right:30px"><svg width="12" height="12" viewBox="0 0 12 12"><path d="M4 1l5 5-5 5" stroke="#fff" stroke-width="2" fill="none"/></svg></a>
  <div class="hero-copy">
    <h1>BRIGHTFIELD HOMES</h1>
    <p>Lorem ipsum dolor sit amet conse ctetur<br>adipiscing elit, sed do eiusmod</p>
    <span class="btn-outline">READ MORE</span>
  </div>
</section>

<section class="features">
  <div class="feature">
    <svg width="80" height="64" viewBox="0 0 80 64" fill="none" stroke="#fff" stroke-width="2.5"><path d="M14 6h54l-8 40H6z"/><path d="M32 6l-8 40M50 6l-8 40M11 20h55M8 33h55"/><path d="M34 46v12M22 58h26"/></svg>
    <h3>BRIGHTFIELD HOMES AS SAFE</h3>
    <p>Lorem ipsum dolor sit amet, consectetur adipiscing elit, sed do eiusmod tempor incididunt ut labore et dolore magna aliqua. Ut enim ad minim veniam, quis nostrud exercitation ullamco laboris nisi ut aliquip</p>
  </div>
  <div class="feature">
    <svg width="66" height="62" viewBox="0 0 66 62" fill="none" stroke="#fff" stroke-width="4" stroke-linecap="round"><path d="M52 30a24 24 0 1 1-10-19"/><path d="M18 30l12 12 30-32"/></svg>
    <h3>RELIABLE AND TRUSTWORTHY</h3>
    <p>Lorem ipsum dolor sit amet, consectetur adipiscing elit, sed do eiusmod tempor incididunt ut labore et dolore magna aliqua. Ut enim ad minim veniam, quis nostrud exercitation ullamco laboris nisi ut aliquip</p>
  </div>
</section>

<section class="welcome">
  <h2>Welcome To <span>Brightfield Homes</span></h2>
  <p>Brightfield Homes is a pioneering approach by councils to support pensioner households to save money and take control of their energy bills by installing affordable, quality solar systems with no upfront costs. Brightfield Homes, based on the City of Marlowe's successful program, ensures that pension card households receive a solar system that pays for itself in electricity savings from day one. Brightfield Homes will be progressively</p>
</section>

<section class="cards">
  <article class="card">
    <div class="photo" role="img" aria-label="Green solar energy concept with leaves and icons" style="background:linear-gradient(135deg,#8fbf3c,#3f7d2a)"></div>
    <h4>Coordinating Household Promotion</h4>
    <p>Lorem ipsum dolor sit amet, consectetur adipiscing elit, sed do eiusmod tempor incididunt ut labore et dolore magna aliqua. Ut enim ad minim veniam,</p>
  </article>
  <article class="card">
    <div class="photo" role="img" aria-label="Installer fitting solar panels on a roof" style="background:linear-gradient(180deg,#3e7fd0,#9cc2ea 60%,#2c3f66)"></div>
    <h4>Administering The Installations</h4>
    <p>Lorem ipsum dolor sit amet, consectetur adipiscing elit, sed do eiusmod tempor incididunt ut labore et dolore magna aliqua. Ut enim ad minim veniam,</p>
  </article>
  <article class="card">
    <div class="photo" role="img" aria-label="Row of modern homes with rooftop solar panels" style="background:linear-gradient(180deg,#7fb0e6,#c8dcf2 55%,#4f5f7a)"></div>
    <h4>Evaluating The Project</h4>
    <p>Lorem ipsum dolor sit amet, consectetur adipiscing elit, sed do eiusmod tempor incididunt ut labore et dolore magna aliqua. Ut enim ad minim veniam,</p>
  </article>
</section>

<section class="how" role="img" aria-label="Close view of solar panels in dark blue tones">
  <h2>HOW IT WORKS</h2>
  <div class="steps">
    <div class="step"><svg width="28" height="28" viewBox="0 0 28 28" fill="none" stroke="#fff" stroke-width="2.5" stroke-linecap="round"><path d="M23 14a10 10 0 1 1-5-8.5"/><path d="M8 13l6 6 12-13"/></svg><span>Brightfield Homes checks that every person gets a solar system that pays for itself in energy savings from day one</span></div>
    <div class="step"><svg width="28" height="28" viewBox="0 0 28 28" fill="none" stroke="#fff" stroke-width="2.5" stroke-linecap="round"><path d="M23 14a10 10 0 1 1-5-8.5"/><path d="M8 13l6 6 12-13"/></svg><span>Brightfield Homes organises for the solar<br>system to be installed</span></div>
    <div class="step"><svg width="28" height="28" viewBox="0 0 28 28" fill="none" stroke="#fff" stroke-width="2.5" stroke-linecap="round"><path d="M23 14a10 10 0 1 1-5-8.5"/><path d="M8 13l6 6 12-13"/></svg><span>Brightfield Homes supports pensioners to understand and get the most out of solar</span></div>
    <div class="step"><svg width="28" height="28" viewBox="0 0 28 28" fill="none" stroke="#fff" stroke-width="2.5" stroke-linecap="round"><path d="M23 14a10 10 0 1 1-5-8.5"/><path d="M8 13l6 6 12-13"/></svg><span>Pensioners gradually pay for cost through their usual rates payments at 0% interest</span></div>
  </div>
  <div class="btn-pill">GET INVOLVED</div>
</section>

<section class="news">
  <h2>LATEST NEWS</h2>
  <div class="news-nav">
    <svg width="10" height="14" viewBox="0 0 10 14"><path d="M7 2L2 7l5 5" stroke="#333" stroke-width="2" fill="none"/></svg>
    <svg width="10" height="14" viewBox="0 0 10 14"><path d="M3 2l5 5-5 5" stroke="#333" stroke-width="2" fill="none"/></svg>
  </div>
  <div class="news-list">
    <article class="news-item">
      <div class="photo" role="img" aria-label="Smiling senior man holding a walking cane" style="background:radial-gradient(circle at 45% 40%,#e8c4a8,#c98a5a 55%,#b5b0a8)"></div>
      <div>
        <h3>Nulla at diam ornare, aliquam urna</h3>
        <time>JAN 25, 2017</time>
        <p>Nulla at diam ornare, aliquam urna vel, commodo urna. Nam id risus a est luctus consectetur quis eget libero. Suspendisse potenti. Pellentesque habitant morbi tristique senectus</p>
        <span class="more">Read More +</span>
      </div>
    </article>
    <article class="news-item">
      <div class="photo" role="img" aria-label="Engineer in hard hat checking a tablet beside solar panels" style="background:radial-gradient(circle at 50% 40%,#bfe4f7,#3aa6dc 60%,#1d6fb0)"></div>
      <div>
        <h3>Nulla at diam ornare, aliquam urna</h3>
        <time>JAN 25, 2017</time>
        <p>Nulla at diam ornare, aliquam urna vel, commodo urna. Nam id risus a est luctus consectetur quis eget libero. Suspendisse potenti. Pellentesque habitant morbi tristique senectus</p>
        <span class="more">Read More +</span>
      </div>
    </article>
  </div>
</section>

<footer class="footer">
  <div class="brand"><span class="dot"></span>Brightfield Homes</div>
  <p class="footer-about">Nemo enim ipsam voluptatem quia voluptas sit aspernatur aut odit aut fugit, sed quia consequuntur magni dolores</p>
  <div class="socials"><span></span><span></span><span></span><span></span></div>

  <div class="col-news">
    <h4>Sign Up For Newsletter</h4>
    <p>Excepteur sint occaecat cupidatat non proident, sunt in culpa qui officia deserunt</p>
    <div class="field">Enter email</div>
    <div class="btn">SUBSCRIPTION</div>
  </div>

  <div class="col-contact">
    <h4>Contact Us</h4>
    <div class="contact-row" style="top:92px">
      <svg width="12" height="16" viewBox="0 0 12 16"><path d="M6 0a6 6 0 0 0-6 6c0 4 6 10 6 10s6-6 6-10a6 6 0 0 0-6-6z" fill="#555"/><circle cx="6" cy="6" r="2.2" fill="#f1f1f1"/></svg>
      <span>Brightfield Homes 12,<br>Wattle Lane, VIC 3999</span>
    </div>
    <div class="contact-row" style="top:152px">
      <svg width="13" height="13" viewBox="0 0 24 24"><path d="M5 2l4 1 1 5-3 2c1 3 3 5 6 6l2-3 5 1 1 4c-1 2-3 3-5 3C9 20 4 15 3 7c0-2 1-4 2-5z" fill="#555"/></svg>
      <span>Phone:&nbsp; 0400 555 217</span>
    </div>
    <div class="contact-row" style="top:184px;font-size:11.5px">
      <svg width="13" height="10" viewBox="0 0 13 10" style="margin-top:6px"><rect width="13" height="10" fill="#555"/><path d="M0 0l6.5 5L13 0" stroke="#f1f1f1" fill="none"/></svg>
      <span>doug.hallett@brightfield.example.au</span>
    </div>
  </div>

  <div class="col-links">
    <h4>Quick Links</h4>
    <ul><li>Home</li><li>About Us</li><li>Services</li><li>Get A Quote</li><li>Blog</li><li>Contact Us</li></ul>
  </div>
</footer>
<div class="bottom-bar">©2017 Brightfield Homes., All Rights Reserved.</div>
</body>
</html>
```